Create modern and sleek business card for luxury real estate company

We're a "boutique" real estate office looking for a design that gets across a highly modern luxury brand. Blacks and whites are probably the best colors unless we try a silver foil for the logo. I've attached a version of our current logo here. I'd like to swap out the current font on there with Gotham Light Regular.

I'm looking to have one side of the card have the logo with the space for our agents info on the other side.

Target Market(s)

Young professionals in a "luxury" headspace

Industry/Entity Type

Real estate

Contact Information for Business Card

A place for agent name, cell number, website. The slogan "Quietly Redefining Fine Homes".

Font styles to use
Other font styles liked:
• Gotham Regular

Colors

Designer to choose only greyscale colors for use in the design.

Requirements
Must have
• Matte black as the background color. Clean lines and use of contrast. A specific design aspect that will use silver foil.
Nice to have
• Up in the air on integrating a QR code
Should not have
• Any houses or other real estate related design (ex: a clip art house)

```html
<!DOCTYPE html>
<html lang="en">
<head>
<meta charset="utf-8">
<title>Halden Realty – Business Card</title>
<link rel="stylesheet" href="https://fonts.googleapis.com/css2?family=Montserrat:wght@300;400;700&display=swap">
<style>
  :root {
    --stage: #1b1b1d;
    --paper: #ffffff;
    --ink: #262628;
    --ink-soft: #8a8a8c;
    --band: #2b2b2e;
    --band-text: #d4d4d6;
    --ghost: #e8e8ea;
    --stripe-dark: #9a9a9c;
    --stripe-light: #c9c9cb;
    --matte: #1f1f22;
    --sheen: #3b3b3f;
    --foil: #f2f2f4;
  }
  * { box-sizing: border-box; margin: 0; padding: 0; }
  html, body { width: 1200px; height: 900px; overflow: hidden; }
  body {
    background: var(--stage);
    font-family: "Montserrat", sans-serif;
    position: relative;
  }
  .card {
    position: absolute;
    left: 260px;
    width: 680px;
    height: 388px;
    overflow: hidden;
    box-shadow: 0 14px 30px rgba(0,0,0,.45);
  }
  /* Front: agent details */
  .card--front { top: 50px; background: var(--paper); }
  .brand {
    position: absolute;
    display: flex;
    align-items: center;
  }
  .brand__dot {
    border-radius: 50%;
    border-style: solid;
    flex: none;
  }
  .brand__name {
    font-weight: 400;
    line-height: 1.05;
    letter-spacing: 1px;
    text-transform: uppercase;
  }
  .card--front .brand { left: 36px; top: 34px; gap: 18px; }
  .card--front .brand__dot { width: 74px; height: 74px; border-width: 2px; border-color: var(--ink); }
  .card--front .brand__name { font-size: 40px; color: var(--ink); }

  .ghost-circle {
    position: absolute;
    right: 44px;
    top: 70px;
    width: 226px;
    height: 226px;
    border-radius: 50%;
    border: 10px solid var(--ghost);
  }
  .agent { position: absolute; left: 60px; top: 196px; }
  .agent__name { font-size: 25px; font-weight: 700; color: var(--ink); }
  .agent__role { font-size: 15px; font-weight: 400; color: var(--ink-soft); margin-top: 2px; }

  .contact {
    position: absolute;
    left: 56px;
    top: 262px;
    list-style: none;
    display: grid;
    gap: 6px;
  }
  .contact__item {
    display: flex;
    align-items: center;
    gap: 26px;
    font-size: 16px;
    font-weight: 400;
    color: var(--ink);
  }
  .contact__item svg { width: 16px; height: 16px; flex: none; }

  .slogan-band {
    position: absolute;
    left: 0;
    bottom: 0;
    width: 470px;
    height: 56px;
    background: var(--band);
    clip-path: polygon(0 0, 95% 0, 100% 100%, 0 100%);
    display: flex;
    align-items: center;
    padding-left: 30px;
  }
  .slogan {
    font-size: 19px;
    font-weight: 300;
    letter-spacing: 1.2px;
    color: var(--band-text);
    text-transform: uppercase;
    white-space: nowrap;
  }
  .stripe {
    position: absolute;
    right: 0;
  }
  .stripe--light { bottom: 70px; width: 262px; height: 3px; background: var(--stripe-light); }
  .stripe--dark { bottom: 58px; width: 240px; height: 7px; background: var(--stripe-dark); }

  /* Back: brand side */
  .card--back {
    top: 462px;
    background: linear-gradient(100deg, var(--matte) 0%, var(--matte) 54%, var(--sheen) 56%, #2c2c30 100%);
  }
  .card--back .brand {
    left: 50%;
    top: 50%;
    transform: translate(-50%, -50%);
    gap: 22px;
  }
  .card--back .brand__dot { width: 96px; height: 96px; border-width: 3px; border-color: var(--foil); }
  .card--back .brand__name { font-size: 50px; color: var(--foil); }
</style>
</head>
<body>

  <section class="card card--front" aria-label="Business card, agent side">
    <div class="brand">
      <span class="brand__dot"></span>
      <span class="brand__name">Halden<br>Realty</span>
    </div>

    <div class="ghost-circle" aria-hidden="true"></div>

    <div class="agent">
      <p class="agent__name">Mara Lindqvist</p>
      <p class="agent__role">Agent</p>
    </div>

    <ul class="contact">
      <li class="contact__item">
        <svg viewBox="0 0 16 16" aria-hidden="true"><rect x="4" y="1" width="8" height="14" rx="1.5" fill="none" stroke="#262628" stroke-width="1.6"/><circle cx="8" cy="12.3" r="0.9" fill="#262628"/></svg>
        555 010 2040
      </li>
      <li class="contact__item">
        <svg viewBox="0 0 16 16" aria-hidden="true"><circle cx="8" cy="8" r="6.5" fill="none" stroke="#262628" stroke-width="1.5"/><ellipse cx="8" cy="8" rx="2.8" ry="6.5" fill="none" stroke="#262628" stroke-width="1.2"/><line x1="1.5" y1="8" x2="14.5" y2="8" stroke="#262628" stroke-width="1.2"/></svg>
        www.haldenrealty.com
      </li>
    </ul>

    <span class="stripe stripe--light" aria-hidden="true"></span>
    <span class="stripe stripe--dark" aria-hidden="true"></span>

    <div class="slogan-band">
      <p class="slogan">Quietly Redefining Fine Homes</p>
    </div>
  </section>

  <section class="card card--back" aria-label="Business card, brand side">
    <div class="brand">
      <span class="brand__dot"></span>
      <span class="brand__name">Halden<br>Realty</span>
    </div>
  </section>

</body>
</html>
```